Business Card Design

New business card design

Target Market(s)

Residential & Commercial Property Managers

Industry/Entity Type

Plumbing Services

Contact Information for Business Card

Name - Rowan Keddle, title - Director, Phone Number - 0431 286 517, email - rowan@tbk-plumbing.com.au, Company ABN - 73 215 904 386,

Font styles to use
Sans Serif

Colors
0054AA
0677BA
7BADD7
CADEEF
E8F1F8

```html
<!DOCTYPE html>
<html lang="en">
<head>
<meta charset="utf-8">
<title>TBK Plumbing Services – Business Card</title>
<link rel="stylesheet" href="https://fonts.googleapis.com/css2?family=Lato:wght@300;400;700&family=Montserrat:wght@700&display=swap">
<style>
  :root {
    --canvas: #2a2d31;
    --ink-dark: #1d232b;
    --ink-text: #1f252c;
    --muted: #6b7178;
    --accent: #18a4e6;
    --paper: #ffffff;
    --paper-shade: #eef0f1;
    --drop-faint: #252d36;
  }
  * { box-sizing: border-box; margin: 0; padding: 0; }
  html, body { width: 1200px; height: 952px; overflow: hidden; }
  body {
    background: var(--canvas);
    font-family: "Lato", sans-serif;
    display: flex;
    align-items: center;
    justify-content: center;
    gap: 40px;
  }
  .card {
    position: relative;
    width: 540px;
    height: 309px;
    border-radius: 4px;
    overflow: hidden;
    box-shadow: 0 14px 30px rgba(0,0,0,0.45);
  }
  .card-art { position: absolute; inset: 0; width: 100%; height: 100%; }

  .brand {
    position: absolute;
    display: flex;
    align-items: center;
    gap: 10px;
    font-family: "Lato", sans-serif;
    font-weight: 300;
    letter-spacing: 0.04em;
    white-space: nowrap;
  }
  .brand-dot {
    width: 12px; height: 12px; border-radius: 50%;
    background: var(--accent);
    flex: none;
  }

  /* Front */
  .card-front { background: var(--ink-dark); }
  .card-front .brand {
    left: 50%; top: 112px; transform: translateX(-50%);
    color: var(--paper);
    font-size: 32px;
  }

  /* Back */
  .card-back { background: var(--ink-dark); }
  .card-back .brand {
    left: 34px; top: 30px;
    color: var(--ink-text);
    font-size: 22px;
  }
  .contact {
    position: absolute;
    left: 34px; top: 88px;
    color: var(--ink-text);
  }
  .contact-name {
    font-family: "Montserrat", sans-serif;
    font-weight: 700;
    font-size: 22px;
    line-height: 1.1;
  }
  .contact-name .given { font-weight: 700; }
  .contact-title {
    font-size: 15px;
    font-weight: 300;
    color: var(--muted);
    margin-top: 2px;
    margin-bottom: 14px;
  }
  .contact-line {
    display: flex; align-items: center; gap: 8px;
    font-size: 13px; font-weight: 300; color: var(--muted);
    margin-bottom: 6px;
  }
  .contact-icon {
    width: 16px; height: 16px; border-radius: 3px;
    background: var(--accent);
    display: flex; align-items: center; justify-content: center;
    flex: none;
  }
  .contact-abn {
    font-size: 14px; font-weight: 700; color: var(--ink-text);
    margin-top: 6px;
  }
  .contact-abn .label { color: var(--accent); font-weight: 400; }
</style>
</head>
<body>

  <section class="card card-front" aria-label="Business card front">
    <svg class="card-art" viewBox="0 0 540 309" aria-hidden="true">
      <circle cx="300" cy="230" r="86" fill="var(--drop-faint)"/>
      <path d="M0 292 H250 C278 292 292 268 322 268 C352 268 364 292 392 300 C402 303 410 309 420 309 H0 Z" fill="var(--accent)"/>
    </svg>
    <div class="brand"><span class="brand-dot"></span>TBK Plumbing Services</div>
  </section>

  <section class="card card-back" aria-label="Business card back">
    <svg class="card-art" viewBox="0 0 540 309" aria-hidden="true">
      <path d="M0 0 H540 V150 C520 200 480 230 440 236 C420 275 380 309 320 309 H0 Z" fill="var(--paper)"/>
      <circle cx="355" cy="235" r="62" fill="var(--paper-shade)"/>
    </svg>
    <div class="brand"><span class="brand-dot"></span>TBK Plumbing Services</div>
    <div class="contact">
      <p class="contact-name">Rowan Keddle</p>
      <p class="contact-title">Director</p>
      <p class="contact-line">
        <span class="contact-icon">
          <svg width="10" height="10" viewBox="0 0 10 10" aria-hidden="true"><path d="M2 1 L4 1 L4.6 3 L3.4 3.8 C4 5.2 4.8 6 6.2 6.6 L7 5.4 L9 6 L9 8 C9 8.6 8.6 9 8 9 C4.5 9 1 5.5 1 2 C1 1.4 1.4 1 2 1 Z" fill="#fff"/></svg>
        </span>0431 286 517
      </p>
      <p class="contact-line">
        <span class="contact-icon">
          <svg width="10" height="8" viewBox="0 0 10 8" aria-hidden="true"><rect x="0.5" y="0.5" width="9" height="7" fill="none" stroke="#fff"/><path d="M0.5 0.5 L5 4.5 L9.5 0.5" fill="none" stroke="#fff"/></svg>
        </span>rowan@tbk-plumbing.com.au
      </p>
      <p class="contact-abn"><span class="label">ABN -</span> 73 215 904 386</p>
    </div>
  </section>

</body>
</html>
```